Garlic Farm for Farm Sales/Restaurant sales

Need a professional, but appealing to agriculture world. We are selling 27 kinds of Organic Garlic from a farm in Simla,CO. I have uploaded logo and business information-we are going to need a template, because I will need to use it for four separate people.
-We are trying to appeal to Farm to table restaurants
-As well as growers/farmers

Target Market(s)

Agriculture Sales/Restaurants-Organic

Industry/Entity Type

Agriculture

Contact Information for Business Card

Want it to look more unique then your average kelto stock card- I want it to look amazing

Font styles to use
Sans Serif

Colors
0455a3
ec1f27
fbed22
ffffff

Requirements
Must have
• Just be creative
Nice to have
• Colorful
Should not have
• plain

```html
<!DOCTYPE html>
<html lang="en">
<head>
<meta charset="utf-8">
<title>Plainsview Garlic Co. – Business Card</title>
<link rel="stylesheet" href="https://fonts.googleapis.com/css2?family=Patrick+Hand&family=Questrial&display=swap">
<style>
  :root {
    --page-bg: #e4e1dc;
    --navy-deep: #0b1838;
    --navy: #1b2d5c;
    --navy-light: #2c4478;
    --garlic-red: #b5121b;
    --brand-red: #ec1f27;
    --gold: #f5c518;
    --frost: #f1efeb;
    --frost-edge: #d9d6d0;
    --ink-light: #e6e9f2;
    --logo-ink: #16254d;
  }
  * { margin: 0; padding: 0; box-sizing: border-box; }
  html, body { width: 1200px; height: 969px; overflow: hidden; }
  body {
    background: var(--page-bg);
    display: flex; align-items: center; justify-content: center;
    font-family: "Questrial", sans-serif;
  }
  .card {
    position: relative;
    width: 1040px; height: 592px;
    border-radius: 30px;
    overflow: hidden;
    background: linear-gradient(135deg, var(--frost) 0%, #fbfaf8 55%, var(--frost-edge) 100%);
    box-shadow: 0 18px 40px rgba(0,0,0,.18);
  }
  .card-shape { position: absolute; inset: 0; }
  .social-row { position: absolute; left: 44px; top: 40px; display: flex; gap: 10px; }
  .social-dot {
    width: 34px; height: 34px; border-radius: 50%;
    border: 2px solid var(--gold);
  }
  .contact { position: absolute; left: 48px; top: 218px; color: var(--ink-light); }
  .contact-name {
    font-family: "Patrick Hand", sans-serif;
    font-size: 46px; color: var(--gold); line-height: 1;
  }
  .contact-title {
    font-family: "Patrick Hand", sans-serif;
    font-size: 30px; margin-top: 10px; line-height: 1;
  }
  .contact-address { margin-top: 34px; font-size: 28px; line-height: 36px; }
  .contact-lines { margin-top: 24px; list-style: none; font-size: 28px; line-height: 40px; }
  .contact-lines li { display: flex; align-items: center; gap: 14px; }
  .contact-lines svg { width: 24px; height: 24px; fill: var(--gold); flex: none; }
  .brand {
    position: absolute; left: 610px; top: 40px; width: 400px;
    display: flex; flex-direction: column; align-items: center;
  }
  .brand-dot {
    width: 120px; height: 120px; border-radius: 50%;
    background: var(--garlic-red);
  }
  .brand-name {
    margin-top: 44px;
    font-size: 40px; color: var(--logo-ink); line-height: 1;
    white-space: nowrap;
  }
</style>
</head>
<body>
  <section class="card" aria-label="Business card for Plainsview Garlic Co.">
    <svg class="card-shape" viewBox="0 0 1040 592" preserveAspectRatio="none" aria-hidden="true">
      <defs>
        <linearGradient id="panel-fill" x1="0" y1="0" x2="1" y2="1">
          <stop offset="0" stop-color="var(--navy-light)"/>
          <stop offset=".55" stop-color="var(--navy)"/>
          <stop offset="1" stop-color="var(--navy-deep)"/>
        </linearGradient>
      </defs>
      <path class="accent-swoosh" d="M410 0 H452 C520 150 560 380 900 592 H820 C560 460 470 250 410 0 Z" fill="var(--garlic-red)"/>
      <path class="accent-line" d="M452 0 C520 150 560 380 900 592" fill="none" stroke="#ffffff" stroke-width="3" opacity=".8"/>
      <path class="navy-panel" d="M0 0 H416 C470 250 560 460 830 592 H0 Z" fill="url(#panel-fill)"/>
    </svg>

    <div class="social-row" aria-label="Social links">
      <span class="social-dot"></span><span class="social-dot"></span>
      <span class="social-dot"></span><span class="social-dot"></span>
    </div>

    <div class="contact">
      <p class="contact-name">Dale Warrick</p>
      <p class="contact-title">CEO/Founder</p>
      <p class="contact-address">P.O. Box 412<br>Ardell, CO&nbsp; 80999</p>
      <ul class="contact-lines">
        <li><svg viewBox="0 0 24 24"><path d="M6.6 10.8a15.1 15.1 0 0 0 6.6 6.6l2.2-2.2a1 1 0 0 1 1-.25 11.4 11.4 0 0 0 3.6.57 1 1 0 0 1 1 1V20a1 1 0 0 1-1 1A17 17 0 0 1 3 4a1 1 0 0 1 1-1h3.5a1 1 0 0 1 1 1c0 1.25.2 2.45.57 3.57a1 1 0 0 1-.25 1z"/></svg>555-014-2297</li>
        <li><svg viewBox="0 0 24 24"><path d="M2 5h20v14H2z M2 5l10 8 10-8" stroke="#0b1838" stroke-width="1.5"/></svg>Hello@PVGarlic.com</li>
        <li><svg viewBox="0 0 24 24"><circle cx="12" cy="12" r="10"/><path d="M2 12h20M12 2c3 3 3 17 0 20M12 2c-3 3-3 17 0 20" fill="none" stroke="#0b1838" stroke-width="1.5"/></svg>www.PVGarlic.com</li>
      </ul>
    </div>

    <div class="brand">
      <span class="brand-dot"></span>
      <p class="brand-name">Plainsview Garlic Co.</p>
    </div>
  </section>
</body>
</html>
```